Tallowmere Cornerstones

Need to improve polish and professionalism of PPT presentation. Get consistent look and feel through whole slides, improved look and feel while maintaining the corporate standards/colour scheme, from the Brackwyn corporate presentation. Need everything in Arial font with colours consistent with the PPT template

```html
<!DOCTYPE html>
<html lang="en">
<head>
<meta charset="utf-8">
<title>Tallowmere Cornerstones – KPI Deck Overview</title>
<link href="https://fonts.googleapis.com/css2?family=Arimo:wght@400;700&display=swap" rel="stylesheet">
<style>
  :root{
    --canvas:#6a9aab;
    --navy:#0d2430;
    --red:#d3272e;
    --white:#ffffff;
    --ink:#1b1b1b;
    --muted:#8a9196;
    --rule-blue:#2c5f86;
    --tu-blue:#8dd0e6;
    --tu-green:#4fdc4f;
    --tu-yellow:#f6f64a;
    --tu-orange:#ee9d70;
    --tu-purple:#b680da;
  }
  *{box-sizing:border-box;margin:0;padding:0}
  html,body{width:1200px;height:1200px;overflow:hidden;background:var(--canvas);font-family:"Arimo",Arial,sans-serif;color:var(--ink)}
  .canvas{position:relative;width:1200px;height:1200px}
  .slide{position:absolute;width:850px;height:478px;background:var(--white);overflow:hidden;transform:scale(.6212);transform-origin:0 0}
  .abs{position:absolute}
  .footer-note{position:absolute;top:461px;font-size:8px;color:var(--muted)}
  .page-no{position:absolute;top:458px;right:14px;font-size:11px}
  .brand{position:absolute;font-weight:700;letter-spacing:.5px;color:var(--navy);display:flex;align-items:center;gap:3px}
  .brand .dot{width:4px;height:4px;background:var(--red)}
  .brand-chip{background:var(--white);padding:3px 7px;font-size:11px}
  .photo{position:absolute}
  .num{position:absolute;width:18px;height:18px;border-radius:50%;background:var(--red);color:#fff;font-size:8px;display:flex;align-items:center;justify-content:center;box-shadow:0 0 0 3px #f6c9cb}
  .card{position:absolute;background:#fff;box-shadow:0 1px 5px rgba(0,0,0,.18);font-size:11.5px;line-height:1.3;color:#333}
  .node{position:absolute;background:#fff;font-weight:700;font-size:13px;text-align:center;display:flex;align-items:center;justify-content:center;line-height:1.2;box-shadow:0 1px 4px rgba(0,0,0,.15)}
  .node.top{border-bottom:2px solid var(--rule-blue)}
  .node.leaf{border-bottom:3px solid var(--red)}
  .tu{position:absolute;border:1px solid #2b2b2b;font-size:10px;font-weight:700;display:flex;align-items:center;justify-content:center;text-align:center;line-height:1.1}
  .cycle-label{position:absolute;font-size:8px;font-weight:700;line-height:1.1;color:#222}
</style>
</head>
<body>
<div class="canvas">

  <!-- Slide 1: title -->
  <section class="slide" style="left:57px;top:48px">
    <svg class="abs" width="850" height="478" style="left:0;top:0">
      <polygon points="85,412 455,412 455,345 445,345 445,401 73,401" fill="var(--red)"/>
      <polygon points="0,0 378,0 455,77 455,400 95,400 0,335" fill="var(--navy)"/>
    </svg>
    <div class="photo" role="img" aria-label="Laptop showing a glowing bar chart above an open hand" style="left:383px;top:55px;width:452px;height:290px;border-radius:10px;background:radial-gradient(ellipse at 50% 45%,#2fc3c8 0%,#0e5868 35%,#0a2a36 70%,#1a2228 100%);border:6px solid #2a2f33;border-bottom-width:14px"></div>
    <div class="abs" style="left:51px;top:100px;color:#fff;font-size:39px;line-height:1;">Tallowmere<br>Cornerstones KPIs</div>
    <div class="abs" style="left:130px;top:203px;color:#fff;font-size:11px">AND</div>
    <div class="abs" style="left:51px;top:218px;color:#fff;font-size:39px;line-height:1;">Production<br>Fundamentals</div>
    <div class="brand" style="left:530px;top:392px;font-size:46px">BRACKWYN<span class="dot" style="width:9px;height:9px"></span></div>
    <div class="footer-note" style="left:18px">© 2024 Brackwyn Mining Solutions Inc.</div>
    <div class="footer-note" style="left:386px">Strictly Confidential</div>
  </section>

  <!-- Slide 2: objectives -->
  <section class="slide" style="left:615px;top:48px">
    <div class="abs" style="left:0;top:0;width:361px;height:478px;background:var(--navy)"></div>
    <div class="abs" style="left:34px;top:96px;color:#fff;font-size:36px;font-weight:700;line-height:1">KPI &amp; Production<br>Fundamentals</div>
    <div class="photo" role="img" aria-label="Yellow mining excavator loading a haul truck in a pit" style="left:0;top:268px;width:361px;height:110px;background:linear-gradient(100deg,#5b646a 0%,#8c8a7a 35%,#c9a33a 60%,#7d7a6d 100%)"></div>
    <div class="brand" style="right:14px;top:14px;font-size:10px">BRACKWYN<span class="dot"></span></div>
    <div class="abs" style="left:403px;top:44px;font-size:17px;font-weight:700">At the end of this module, you will understand</div>
    <div class="abs" style="left:403px;top:96px;font-size:13px;color:#333">Understand the key concepts of mine production KPIs</div>
    <div class="num" style="left:406px;top:133px">1</div><div class="abs" style="left:433px;top:134px;font-size:12px">Time Usage Model</div>
    <div class="num" style="left:406px;top:163px">2</div><div class="abs" style="left:433px;top:164px;font-size:12px">Availability, Utilization and Productivity</div>
    <div class="num" style="left:406px;top:193px">3</div><div class="abs" style="left:433px;top:194px;font-size:12px">Elements of the haul cycle</div>
    <div class="num" style="left:406px;top:223px">4</div><div class="abs" style="left:433px;top:224px;font-size:12px">Elements of the loading cycle</div>
    <div class="num" style="left:406px;top:253px">5</div><div class="abs" style="left:433px;top:254px;font-size:12px">How changes in each of these elements impact mine production</div>
    <div class="card" style="left:408px;top:295px;width:122px;height:143px;padding:18px 10px 0 10px;border-bottom:3px solid #fff">The goal will be to create a baseline of understanding and a common language across the entire mine-ops team<span class="abs" style="right:0;bottom:-3px;width:24px;height:3px;background:var(--rule-blue)"></span></div>
    <div class="card" style="left:546px;top:295px;width:124px;height:143px;padding:20px 12px 0 12px">You may already understand these concepts<span class="abs" style="right:0;bottom:0;width:24px;height:3px;background:var(--rule-blue)"></span></div>
    <div class="card" style="left:686px;top:295px;width:124px;height:143px;padding:18px 12px 0 12px">This is the time to ask questions and get clarification!<span class="abs" style="right:0;bottom:0;width:24px;height:3px;background:var(--rule-blue)"></span></div>
    <div class="footer-note" style="left:18px;color:#b9c1c6">© 2024 Brackwyn Mining Solutions Inc.</div>
    <div class="footer-note" style="left:386px">Strictly Confidential</div>
    <div class="page-no">2</div>
  </section>

  <!-- Slide 3: what makes up production (light) -->
  <section class="slide" style="left:57px;top:382px">
    <div class="brand" style="left:0;width:431px;justify-content:center;top:33px;font-size:11px">BRACKWYN<span class="dot"></span></div>
    <div class="abs" style="left:0;width:431px;top:88px;text-align:center;font-size:43px;font-weight:700;line-height:1">What Makes<br>Up Production</div>
    <div class="abs" style="left:0;width:431px;top:192px;text-align:center;font-size:13px">In its simplest terms, we calculate production like this:</div>
    <svg class="abs" width="431" height="478" style="left:0;top:0">
      <polyline points="202,280 202,298 175,298 175,327" fill="none" stroke="#333"/>
      <polyline points="224,280 224,298 251,298 251,327" fill="none" stroke="#333"/>
    </svg>
    <div class="node top" style="left:140px;top:243px;width:146px;height:37px">Production</div>
    <div class="node leaf" style="left:46px;top:327px;width:146px;height:46px">Equipment<br>Productivity</div>
    <div class="node leaf" style="left:232px;top:327px;width:146px;height:46px">Operating Time</div>
    <div class="abs" style="left:431px;top:0;width:419px;height:478px;background:var(--navy)"></div>
    <div class="photo" role="img" aria-label="Row of yellow haul trucks on a mine road" style="left:431px;top:18px;width:419px;height:182px;background:linear-gradient(160deg,#9a9a94 0%,#6d6c66 45%,#b48a2a 70%,#5a5a55 100%)"></div>
    <div class="abs" style="left:479px;top:225px;color:#fff;font-size:13px">This is true for any process</div>
    <div class="card" style="left:480px;top:253px;width:97px;height:96px;text-align:center;color:#444">
      <svg width="44" height="44" viewBox="0 0 44 44" style="margin-top:14px"><circle cx="22" cy="22" r="17" fill="none" stroke="#333" stroke-width="2.5"/><circle cx="22" cy="22" r="5" fill="none" stroke="#333" stroke-width="2"/><path d="M6 20 H17 M27 20 H38 M22 27 V39" stroke="#333" stroke-width="2.5"/></svg>
      <div style="font-size:12px">Driving</div></div>
    <div class="card" style="left:598px;top:253px;width:97px;height:96px;text-align:center;color:#444">
      <svg width="50" height="40" viewBox="0 0 50 40" style="margin-top:12px"><path d="M4 28 V16 H14 L18 8 H44 V28 Z" fill="none" stroke="#333" stroke-width="2"/><circle cx="13" cy="31" r="5" fill="#fff" stroke="#333" stroke-width="2"/><circle cx="37" cy="31" r="5" fill="#fff" stroke="#333" stroke-width="2"/></svg>
      <div style="font-size:12px;line-height:1">Mine<br>Production</div></div>
    <div class="card" style="left:715px;top:253px;width:97px;height:96px;text-align:center;color:#444">
      <svg width="44" height="40" viewBox="0 0 44 40" style="margin-top:12px"><path d="M8 4 L22 24" stroke="#333" stroke-width="2.5"/><rect x="18" y="22" width="20" height="8" fill="none" stroke="#333" stroke-width="2"/><circle cx="22" cy="33" r="4" fill="#fff" stroke="#333" stroke-width="2"/><circle cx="35" cy="33" r="4" fill="#fff" stroke="#333" stroke-width="2"/></svg>
      <div style="font-size:12px;line-height:1">Mowing<br>the lawn</div></div>
    <svg class="abs" width="36" height="44" style="left:480px;top:382px" viewBox="0 0 36 44"><path d="M10 42 V4 M3 11 L10 3 L17 11 M26 2 V40 M19 33 L26 41 L33 33" fill="none" stroke="#fff" stroke-width="3"/></svg>
    <div class="abs" style="left:529px;top:383px;width:280px;color:#fff;font-size:13px;line-height:1.3">Production goes up or down because of a change in Equipment Productivity or Operating Time</div>
    <div class="footer-note" style="left:18px">© 2024 Brackwyn Mining Solutions Inc.</div>
    <div class="footer-note" style="left:386px">Strictly Confidential</div>
    <div class="page-no" style="color:#fff">3</div>
  </section>

  <!-- Slide 4: what makes up production (dark) -->
  <section class="slide" style="left:615px;top:382px">
    <div class="abs" style="left:0;top:0;width:418px;height:478px;background:var(--navy)"></div>
    <div class="brand brand-chip" style="left:175px;top:28px">BRACKWYN<span class="dot"></span></div>
    <div class="abs" style="left:0;width:418px;top:88px;text-align:center;font-size:43px;font-weight:700;line-height:1;color:#fff">What Makes<br>Up Production</div>
    <div class="abs" style="left:0;width:418px;top:192px;text-align:center;font-size:13px;color:#fff">In its simplest terms, we calculate production like this:</div>
    <svg class="abs" width="418" height="478" style="left:0;top:0">
      <polyline points="201,280 201,298 175,298 175,327" fill="none" stroke="#fff"/>
      <polyline points="224,280 224,298 252,298 252,327" fill="none" stroke="#fff"/>
    </svg>
    <div class="node top" style="left:139px;top:243px;width:146px;height:37px">Production</div>
    <div class="node leaf" style="left:46px;top:327px;width:146px;height:46px">Equipment<br>Productivity</div>
    <div class="node leaf" style="left:231px;top:327px;width:146px;height:46px">Operating Time</div>
    <div class="card" style="left:458px;top:42px;width:158px;height:183px;padding:67px 20px 0 20px">Operating time is the time when a piece of equipment is performing it's primary function</div>
    <div class="num" style="left:572px;top:53px;width:30px;height:30px;font-size:16px">1</div>
    <div class="card" style="left:645px;top:42px;width:158px;height:183px;padding:48px 14px 0 14px">To better understand, communicate and discuss the different categories of how we calculate operating time, we use something called a Time Usage Model</div>
    <div class="num" style="left:756px;top:47px;width:30px;height:30px;font-size:16px">2</div>
    <div class="card" style="left:458px;top:255px;width:158px;height:183px;padding:66px 16px 0 16px">Each industry has its own time usage model, and they can vary slightly from industry to industry</div>
    <div class="num" style="left:572px;top:268px;width:30px;height:30px;font-size:16px">3</div>
    <div class="card" style="left:645px;top:255px;width:158px;height:183px;padding:62px 20px 0 20px">Even within an industry, (e.g. Mining) a Time Usage Model can vary from operation to operation</div>
    <div class="num" style="left:756px;top:268px;width:30px;height:30px;font-size:16px">4</div>
    <div class="footer-note" style="left:18px;color:#b9c1c6">© 2024 Brackwyn Mining Solutions Inc.</div>
    <div class="footer-note" style="left:386px;color:#b9c1c6">Strictly Confidential</div>
    <div class="page-no">4</div>
  </section>

  <!-- Slide 5: time usage model -->
  <section class="slide" style="left:57px;top:715px">
    <div class="photo" role="img" aria-label="Aerial view of an open-pit mine with haul trucks and shovels" style="left:0;top:0;width:850px;height:172px;background:linear-gradient(90deg,#0d2430 0%,#1d3a47 40%,#4d6f7c 75%,#3a5a66 100%)"></div>
    <div class="brand brand-chip" style="right:10px;top:10px">BRACKWYN<span class="dot"></span></div>
    <div class="abs" style="left:62px;top:30px;color:#fff;font-size:43px;font-weight:700;line-height:1">Generic Time<br>Usage Model</div>
    <div class="tu" style="left:62px;top:160px;width:738px;height:31px;background:var(--tu-blue);font-weight:400;font-size:10px">CALENDER TIME</div>
    <div class="tu" style="left:62px;top:191px;width:529px;height:30px;background:var(--tu-blue);font-weight:400">AVAILABLE TIME</div>
    <div class="tu" style="left:591px;top:191px;width:209px;height:30px;background:var(--tu-orange);font-weight:400">DOWN</div>
    <div class="tu" style="left:62px;top:221px;width:320px;height:31px;background:var(--tu-blue);font-weight:400">OPERATING TIME</div>
    <div class="tu" style="left:382px;top:221px;width:105px;height:65px;background:var(--tu-green)">OPERATING<br>DELAY</div>
    <div class="tu" style="left:487px;top:221px;width:104px;height:65px;background:var(--tu-yellow)">STANDBY<br>TIME</div>
    <div class="tu" style="left:591px;top:221px;width:105px;height:65px;background:var(--tu-orange)">UNSHEDULED</div>
    <div class="tu" style="left:696px;top:221px;width:104px;height:65px;background:var(--tu-orange)">SHEDULED</div>
    <div class="tu" style="left:62px;top:252px;width:160px;height:34px;background:var(--tu-blue)">EFFECTIVE TIME</div>
    <div class="tu" style="left:222px;top:252px;width:160px;height:34px;background:var(--tu-purple);font-weight:400">NON-EFFECTIVE TIME</div>
    <div class="abs" style="left:0;width:850px;top:319px;text-align:center;font-size:11px">THIS IS A GENERIC MINING TIME USAGE MODEL</div>
    <div class="abs" style="left:399px;top:344px;width:58px;height:1px;background:var(--red)"></div>
    <div class="abs" style="left:160px;width:530px;top:370px;text-align:center;font-size:13px;line-height:1.35">There may be variations from mine-to-mine (ie Utilized time vs Operating Time) but this model describes everything mine operations needs to know about the time usage of a piece of equipment</div>
    <div class="footer-note" style="left:18px">© 2024 Brackwyn Mining Solutions Inc.</div>
    <div class="footer-note" style="left:386px">Strictly Confidential</div>
    <div class="page-no">5</div>
  </section>

  <!-- Slide 6: haul cycle -->
  <section class="slide" style="left:615px;top:715px">
    <svg class="abs" width="850" height="478" style="left:0;top:0">
      <polygon points="0,0 418,0 387,183 0,210" fill="var(--navy)"/>
      <circle cx="606" cy="253" r="170" fill="none" stroke="#555" stroke-width="1" stroke-dasharray="3 3"/>
      <circle cx="606" cy="253" r="181" fill="none" stroke="#eee" stroke-width="6"/>
      <g fill="none" stroke="var(--red)" stroke-width="2" marker-end="url(#arrowhead)">
        <path d="M530 130 Q560 108 598 112"/>
        <path d="M675 84 L700 72"/>
        <path d="M690 115 Q715 140 725 160"/>
        <path d="M750 225 L750 248"/>
        <path d="M735 320 Q728 345 713 355"/>
        <path d="M650 390 Q615 403 580 394"/>
        <path d="M500 315 Q468 282 468 252"/>
        <path d="M472 200 L478 180"/>
        <path d="M510 360 L485 365"/>
      </g>
      <defs><marker id="arrowhead" markerWidth="6" markerHeight="6" refX="4" refY="3" orient="auto"><path d="M0 0 L6 3 L0 6 Z" fill="var(--red)"/></marker></defs>
    </svg>
    <div class="abs" style="left:52px;top:25px;color:#fff;font-size:34px;font-weight:700;line-height:1.02">Equipment<br>Productivity<br>–<br>Haul Trucks</div>
    <div class="brand" style="right:14px;top:14px;font-size:10px">BRACKWYN<span class="dot"></span></div>
    <div class="abs" style="left:32px;top:228px;font-size:13px;font-weight:700;line-height:1.3">To minimize cycle time we reduce the time<br>it takes for each haul cycle element</div>
    <div class="num" style="left:34px;top:286px;width:15px;height:15px;font-size:7px">1</div><div class="abs" style="left:57px;top:288px;font-size:10px;color:#333">The first step is to try to reduce non-effective time in a haul cycle</div>
    <div class="num" style="left:34px;top:314px;width:15px;height:15px;font-size:7px">2</div><div class="abs" style="left:57px;top:316px;font-size:10px;color:#333">What are the non-effective elements of the haul cycle?</div>
    <div class="num" style="left:34px;top:343px;width:15px;height:15px;font-size:7px">3</div><div class="abs" style="left:57px;top:345px;font-size:10px;color:#333">What are some ways to reduce non-effective time in a haul cycle?</div>
    <div class="num" style="left:34px;top:374px;width:15px;height:15px;font-size:7px">4</div><div class="abs" style="left:57px;top:376px;font-size:10px;color:#333">What are the effective elements of a haul cycle?</div>
    <div class="num" style="left:34px;top:403px;width:15px;height:15px;font-size:7px">5</div><div class="abs" style="left:57px;top:405px;font-size:10px;color:#333">What are some way to reduce effective time in a haul cycle?</div>

    <div class="photo" role="img" aria-label="Haul truck traveling empty" style="left:715px;top:62px;width:62px;height:28px;border-radius:4px;background:linear-gradient(#f2cf38,#8a7a3a)"></div>
    <div class="photo" role="img" aria-label="Haul truck stopped empty" style="left:612px;top:95px;width:62px;height:32px;border-radius:4px;background:linear-gradient(#f2cf38,#8a7a3a)"></div>
    <div class="photo" role="img" aria-label="Haul truck dumping" style="left:490px;top:125px;width:52px;height:38px;border-radius:4px;background:linear-gradient(#a07848,#f2cf38)"></div>
    <div class="photo" role="img" aria-label="Haul truck waiting at shovel" style="left:697px;top:175px;width:56px;height:38px;border-radius:4px;background:linear-gradient(#f2cf38,#8a7a3a)"></div>
    <div class="photo" role="img" aria-label="Loaded haul truck waiting at dump" style="left:442px;top:218px;width:58px;height:38px;border-radius:4px;background:linear-gradient(#a07848,#f2cf38)"></div>
    <div class="photo" role="img" aria-label="Haul truck spotting under shovel" style="left:684px;top:263px;width:62px;height:32px;border-radius:4px;background:linear-gradient(#f2cf38,#8a7a3a)"></div>
    <div class="photo" role="img" aria-label="Haul truck being loaded" style="left:655px;top:325px;width:55px;height:40px;border-radius:4px;background:linear-gradient(#a07848,#f2cf38)"></div>
    <div class="photo" role="img" aria-label="Loaded haul truck traveling full" style="left:540px;top:340px;width:58px;height:40px;border-radius:4px;background:linear-gradient(#a07848,#f2cf38)"></div>
    <div class="photo" role="img" aria-label="Loaded haul truck stopped full" style="left:415px;top:355px;width:56px;height:40px;border-radius:4px;background:linear-gradient(#a07848,#f2cf38)"></div>

    <div class="cycle-label" style="left:777px;top:70px">TRAVELING<br>EMPTY</div>
    <div class="cycle-label" style="left:623px;top:137px">STOPPED<br>EMPTY</div>
    <div class="cycle-label" style="left:436px;top:127px">DUMPING</div>
    <div class="cycle-label" style="left:772px;top:184px">WAIT/QUEUE<br>AT SHOVEL</div>
    <div class="cycle-label" style="left:380px;top:212px">WAIT/QUEUE<br>AT DUMP</div>
    <div class="cycle-label" style="left:779px;top:280px">SPOTTING</div>
    <div class="cycle-label" style="left:545px;top:319px">TRAVELING<br>FULL</div>
    <div class="cycle-label" style="left:398px;top:339px">STOPPED<br>FULL</div>
    <div class="cycle-label" style="left:723px;top:378px">LOADING</div>
    <div class="footer-note" style="left:18px">© 2024 Brackwyn Mining Solutions Inc.</div>
    <div class="footer-note" style="left:386px">Strictly Confidential</div>
    <div class="page-no">14</div>
  </section>

</div>
</body>
</html>
```